MRT Property - Business Cards

Looking for a business card & general letterhead, signage etc design for our new logo.

Colours:
000a20
0056a2
00b5ef
0088ce
68cef2

Fonts:
Poppins
Karla

Please keep look and feel of new brand - example in the zip package I sent.

```html
<!DOCTYPE html>
<html lang="en">
<head>
<meta charset="utf-8">
<title>MRT Property – Business Cards</title>
<link rel="stylesheet" href="https://fonts.googleapis.com/css2?family=Karla:wght@400;500&family=Poppins:wght@500;600;700&display=swap">
<style>
  :root {
    --backdrop: #232323;
    --card: #0b1020;
    --navy: #000a20;
    --brand-blue: #0056a2;
    --brand-cyan: #00b5ef;
    --brand-mid: #0088ce;
    --brand-light: #68cef2;
    --front-mark: #3a4560;
    --text-light: #f2f4f8;
  }
  * { box-sizing: border-box; margin: 0; padding: 0; }
  html, body {
    width: 1200px; height: 780px; overflow: hidden;
    background: var(--backdrop);
  }
  .canvas {
    width: 1200px; height: 780px;
    display: flex; align-items: center; justify-content: center; gap: 48px;
  }
  .card {
    position: relative;
    width: 532px; height: 304px;
    background: var(--card);
    border-radius: 24px;
    border: 3px solid var(--brand-cyan);
    box-shadow: 0 14px 30px rgba(0,0,0,.55);
    overflow: hidden;
  }

  /* Front */
  .card--front { display: flex; align-items: center; justify-content: center; }
  .front-brand {
    display: flex; align-items: center; gap: 18px;
    font-family: "Poppins", sans-serif; font-weight: 700;
    font-size: 54px; color: var(--front-mark); letter-spacing: .5px;
  }
  .front-brand__dot {
    width: 46px; height: 46px; border-radius: 50%;
    background: var(--front-mark);
  }

  /* Back */
  .brand {
    position: absolute; left: 34px; top: 38px;
    display: flex; align-items: center; gap: 12px;
    font-family: "Poppins", sans-serif; font-weight: 700;
    font-size: 30px; color: var(--brand-blue);
  }
  .brand__dot {
    width: 30px; height: 30px; border-radius: 50%;
    background: var(--brand-mid);
  }
  .person {
    position: absolute; right: 30px; top: 42px;
    text-align: right; padding-right: 16px;
    border-right: 9px solid var(--brand-blue);
  }
  .person__name {
    font-family: "Poppins", sans-serif; font-weight: 600;
    font-size: 20px; color: var(--brand-blue); letter-spacing: .6px;
    line-height: 1.15;
  }
  .person__role {
    font-family: "Karla", sans-serif; font-weight: 500;
    font-size: 14px; color: var(--text-light); letter-spacing: .4px;
  }
  .address {
    position: absolute; left: 42px; top: 162px;
    font-family: "Karla", sans-serif; font-size: 14px;
    color: var(--text-light); line-height: 1.35; letter-spacing: .3px;
  }
  .contacts {
    position: absolute; left: 42px; bottom: 22px;
    list-style: none;
    font-family: "Karla", sans-serif; font-size: 14px;
    color: var(--text-light); letter-spacing: .3px;
  }
  .contacts li { display: flex; align-items: center; gap: 8px; line-height: 1.55; }
  .contacts svg { width: 13px; height: 13px; flex: none; }
  .icon { fill: none; stroke: var(--brand-cyan); stroke-width: 2; stroke-linecap: round; stroke-linejoin: round; }
</style>
</head>
<body>
<main class="canvas">
  <section class="card card--front" aria-label="Card front">
    <div class="front-brand">
      <span class="front-brand__dot"></span>
      <span>MRT Property</span>
    </div>
  </section>

  <section class="card card--back" aria-label="Card back">
    <div class="brand">
      <span class="brand__dot"></span>
      <span>MRT Property</span>
    </div>

    <div class="person">
      <p class="person__name">DANIEL HART</p>
      <p class="person__role">Managing Director</p>
    </div>

    <p class="address">Your address, City<br>State, Zip 1234</p>

    <ul class="contacts">
      <li>
        <svg viewBox="0 0 24 24"><path class="icon" d="M5 3h4l2 5-2.5 1.5a11 11 0 0 0 6 6L16 13l5 2v4a2 2 0 0 1-2 2A17 17 0 0 1 3 5a2 2 0 0 1 2-2z"/></svg>
        123 456 789
      </li>
      <li>
        <svg viewBox="0 0 24 24"><rect class="icon" x="3" y="5" width="18" height="14" rx="2"/><path class="icon" d="M3 7l9 6 9-6"/></svg>
        info@youremail.com
      </li>
      <li>
        <svg viewBox="0 0 24 24"><circle class="icon" cx="12" cy="12" r="9"/><path class="icon" d="M3 12h18M12 3a14 14 0 0 1 0 18M12 3a14 14 0 0 0 0 18"/></svg>
        www.yourwebsite.com
      </li>
    </ul>
  </section>
</main>
</body>
</html>
```